Verdant Systems Business Card

want the back of card to be blue- with the logo in the center
front of card- info plus logo (info being mailing address, email address, and website address )
4 different names with titles to have on cards
1) Calvin Borsted - Owner
2) Naomi Trelvik- Customer Relationship Specialist
3) Felix Andrade- Vice President of Sales
4) Owen Markby- Chief Technology Officer

Target Market(s)

tech company in the government/probation office industry

Industry/Entity Type

Government Office

Contact Information for Business Card

1) Calvin Borsted - Owner

Colors
0355a3
ffffff

Requirements
Must have
• back side should be blue, with the logo placed in the center
• front side needs to include both the logo, as well as company info (info should include website address, email address, and mailing address)

```html
<!DOCTYPE html>
<html lang="en">
<head>
<meta charset="utf-8">
<title>Verdant Systems Business Card</title>
<link href="https://fonts.googleapis.com/css2?family=PT+Serif&family=Roboto:wght@400&display=swap" rel="stylesheet">
<style>
  :root {
    --navy: #263864;
    --navy-text: #2a3a6b;
    --white: #ffffff;
    --paper: #f7f7f6;
    --grey-text: #7d7f86;
    --grey-band: #9a9aa3;
    --backdrop: #a7a4a4;
  }
  html, body {
    margin: 0;
    width: 1200px;
    height: 1200px;
    overflow: hidden;
    background: var(--backdrop);
  }
  .canvas { position: relative; width: 1200px; height: 1200px; }
  .card {
    position: absolute;
    width: 713px;
    height: 418px;
    border-radius: 24px;
    overflow: hidden;
  }
  .card-back { left: 238px; top: 118px; background: var(--navy); }
  .card-front { left: 232px; top: 645px; background: var(--paper); }

  .brand-name {
    font-family: "PT Serif", serif;
    font-weight: 400;
    margin: 0;
    white-space: nowrap;
    letter-spacing: 2px;
  }
  .card-back .brand-name {
    position: absolute;
    left: 0; right: 0; top: 170px;
    text-align: center;
    color: var(--white);
    font-size: 62px;
  }

  .front-logo { position: absolute; left: 40px; top: 60px; display: flex; align-items: center; gap: 22px; }
  .front-logo .mark { width: 56px; height: 56px; background: var(--navy); }
  .card-front .brand-name { color: var(--navy-text); font-size: 40px; }

  .person { position: absolute; left: 37px; top: 285px; }
  .person-name {
    font-family: "PT Serif", serif;
    color: var(--navy-text);
    font-size: 25px;
    letter-spacing: 0.5px;
    margin: 0 0 4px;
  }
  .person-title { font-family: "Roboto", sans-serif; color: var(--grey-text); font-size: 17px; margin: 0; }

  .contact {
    position: absolute;
    left: 363px; top: 228px;
    font-family: "Roboto", sans-serif;
    color: var(--grey-text);
    font-size: 17px;
    line-height: 28px;
  }
  .address { margin: 0 0 6px; }
  .contact-line { display: flex; align-items: center; gap: 18px; height: 26px; }
  .contact-line svg { width: 18px; height: 16px; fill: var(--navy); }

  .footer-bands { position: absolute; left: 0; bottom: 0; }
  .website {
    position: absolute;
    left: 363px; top: 378px;
    font-family: "Roboto", sans-serif;
    color: var(--white);
    font-size: 17px;
    margin: 0;
  }
</style>
</head>
<body>
<main class="canvas">
  <section class="card card-back" aria-label="Card back">
    <p class="brand-name">VERDANT SYSTEMS</p>
  </section>

  <section class="card card-front" aria-label="Card front">
    <div class="front-logo">
      <div class="mark"></div>
      <p class="brand-name">VERDANT SYSTEMS</p>
    </div>

    <div class="person">
      <p class="person-name">NAOMI TRELVIK</p>
      <p class="person-title">Customer Relationship Specialist</p>
    </div>

    <div class="contact">
      <p class="address">58 Fernbrook Ave., Lakeview,<br>Any Town, US 104872</p>
      <div class="contact-line">
        <svg viewBox="0 0 18 16" aria-hidden="true"><path d="M1 5c0-2 3-4 8-4s8 2 8 4v1h-4V4.5H5V6H1z"/><rect x="3" y="7" width="12" height="8" rx="1.5"/></svg>
        <span>555-014-2290</span>
      </div>
      <div class="contact-line">
        <svg viewBox="0 0 18 16" aria-hidden="true"><path d="M1 2h16v12H1z M1 2l8 7 8-7" fill="var(--navy)" stroke="var(--paper)" stroke-width="1.2"/></svg>
        <span>naomi.t@verdantsystems.com</span>
      </div>
    </div>

    <svg class="footer-bands" width="713" height="60" viewBox="0 0 713 60" aria-hidden="true">
      <rect x="0" y="40" width="330" height="20" fill="var(--grey-band)"/>
      <path d="M313 60 L335 10 L713 10 L713 60 Z" fill="var(--navy)"/>
    </svg>
    <p class="website">www.verdantsystems.com</p>
  </section>
</main>
</body>
</html>
```